Lume wine label

Get all the info (Picture of another bottle & Logo) on a label on a thin wrap label, label size 1.5" width and 11-12" length. Also need Wine Name "LUME" and grape varietal "Gamay" and "Alc. By Vol. 12.8%"

```html
<!DOCTYPE html>
<html lang="en">
<head>
<meta charset="utf-8">
<title>Lume Gamay – Wrap Label</title>
<link rel="stylesheet" href="https://fonts.googleapis.com/css2?family=Playfair+Display:wght@400;700&display=swap">
<style>
  :root {
    --page: #ffffff;
    --cream: #efe8d8;
    --ink: #1c1a19;
    --rose: #c9676f;
    --floral-dark: #3b3733;
    --floral-mid: #6e685f;
    --floral-light: #8f897e;
  }
  * { margin: 0; padding: 0; box-sizing: border-box; }
  html, body {
    width: 1200px;
    height: 391px;
    overflow: hidden;
    background: var(--page);
  }
  .canvas {
    position: relative;
    width: 1200px;
    height: 391px;
  }
  .wrap-label {
    position: absolute;
    left: 85px;
    top: 114px;
    width: 996px;
    height: 137px;
    overflow: hidden;
    background: var(--cream);
  }
  .floral-field {
    position: absolute;
    inset: 0;
    background: linear-gradient(90deg,
      var(--floral-light) 0%,
      var(--floral-mid) 18%,
      var(--floral-dark) 42%,
      var(--floral-mid) 58%,
      var(--floral-dark) 74%,
      var(--floral-light) 100%);
  }
  .title-diamond {
    position: absolute;
    left: 155px;
    top: -65px;
    width: 267px;
    height: 267px;
  }
  .title-block {
    position: absolute;
    left: 155px;
    top: 0;
    width: 267px;
    height: 137px;
    text-align: center;
    font-family: "Playfair Display", serif;
    color: var(--ink);
  }
  .name-mark {
    position: absolute;
    left: 50%;
    top: 22px;
    width: 16px;
    height: 16px;
    margin-left: -8px;
    border-radius: 50%;
    background: var(--ink);
  }
  .wine-name {
    position: absolute;
    left: 0; right: 0;
    top: 44px;
    font-size: 34px;
    font-weight: 700;
    letter-spacing: 1px;
    line-height: 1;
  }
  .varietal {
    position: absolute;
    left: 0; right: 0;
    top: 83px;
    font-size: 11px;
    letter-spacing: 4px;
    line-height: 1;
    color: var(--rose);
  }
  .abv {
    position: absolute;
    left: 0; right: 0;
    top: 118px;
    font-size: 8px;
    letter-spacing: 1px;
    line-height: 1;
  }
  .producer-badge {
    position: absolute;
    left: 779px;
    top: 40px;
    width: 96px;
    height: 59px;
    background: var(--cream);
    border: 2px solid var(--rose);
    text-align: center;
    font-family: "Playfair Display", serif;
    color: var(--ink);
  }
  .producer-label {
    margin-top: 5px;
    font-size: 7px;
    line-height: 1;
  }
  .producer-name {
    margin-top: 11px;
    font-size: 13px;
    font-weight: 700;
    line-height: 1;
  }
</style>
</head>
<body>
  <main class="canvas">
    <section class="wrap-label">
      <div class="floral-field" role="img" aria-label="Black and cream engraved floral pattern of dahlias, lilies and leaves filling the label"></div>

      <svg class="title-diamond" viewBox="0 0 268 268" aria-hidden="true">
        <polygon points="134,0 268,134 134,268 0,134" fill="var(--rose)"/>
        <polygon points="134,12 256,134 134,256 12,134" fill="var(--cream)"/>
      </svg>

      <div class="title-block">
        <span class="name-mark" aria-hidden="true"></span>
        <h1 class="wine-name">LUME</h1>
        <p class="varietal">Gamay</p>
        <p class="abv">Alc. By Vol. 12.8%</p>
      </div>

      <div class="producer-badge">
        <p class="producer-label">Produced by:</p>
        <p class="producer-name">Hollow Lane</p>
      </div>
    </section>
  </main>
</body>
</html>
```